KOVA! Card

The single side "business card" will be utilized to write down product information for our customers. The card needs to include our logo in josefin font and read KOVA! on the front. Our brand colors are espresso brown and copper. The back needs to be white (blank) to allow us to write information down. We want modern, bold, clean and fun.
I have attached a copy of our logo but you do not have to utilize exactly as shown.

```html
<!DOCTYPE html>
<html lang="en">
<head>
<meta charset="utf-8">
<title>KOVA! Card</title>
<link rel="stylesheet" href="https://fonts.googleapis.com/css2?family=Josefin+Sans:wght@300;400&display=swap">
<style>
  :root {
    --copper: #c3390b;
    --paper: #ffffff;
  }
  html, body {
    margin: 0;
    padding: 0;
    width: 1200px;
    height: 686px;
    overflow: hidden;
    background: var(--paper);
  }
  .card {
    display: block;
    width: 1200px;
    height: 686px;
  }
  .card__frame { fill: var(--copper); }
  .card__panel { fill: var(--paper); }
  .brand__mark { fill: var(--copper); }
  .brand__name,
  .brand__tagline,
  .card__headline {
    fill: var(--copper);
    font-family: "Josefin Sans", sans-serif;
    font-weight: 300;
  }
  .brand__name { font-size: 58px; letter-spacing: 6px; }
  .brand__tagline { font-size: 28px; letter-spacing: 3px; }
  .card__headline { font-size: 350px; }
</style>
</head>
<body>
<svg class="card" viewBox="0 0 1200 686" xmlns="http://www.w3.org/2000/svg" role="img" aria-label="KOVA! card for Halvorsen Goldsmith Atelier">
  <rect class="card__frame" x="0" y="0" width="1200" height="686"/>
  <rect class="card__panel card__panel--top" x="32" y="32" width="1136" height="375"/>
  <rect class="card__panel card__panel--write" x="32" y="441" width="1136" height="210"/>

  <g class="brand">
    <rect class="brand__mark" x="42" y="52" width="40" height="40"/>
    <text class="brand__name" x="98" y="92">HALVORSEN</text>
    <text class="brand__tagline" x="42" y="138">Goldsmith Atelier</text>
  </g>

  <text class="card__headline" x="36" y="411" textLength="1142" lengthAdjust="spacing">KOVA!</text>
</svg>
</body>
</html>
```